energy rating company

Web Design graphics and layout only

To create two pages for the website. First the home page and the second is the design for the job board for our clients use after login. I have attached files that explain in detail what the pages should have and the purpose/desires of each object. Please read these thoroughly.

The webpages need to be clean, professional, easy on the eye, obvious in all its buttons and functions with a strong call to action on the home page and branding and clean, great and obvious looking buttons and very simple but dynamic as well. We wish to be seen as contemporary.

Business Concept

Our business concept is simple, to build a website whereby our clients will be able to upload jobs for energy raters to quote on and subsequent complete the work if their quote is selected. To link energy ratings that are required with energy raters via our website. Similarly to the velk website, jobs will be “advertised” on the job board and raters will select which jobs they wish to quote for.

I have attached a Word document explaining all the parts of the website and another word document showing what we are sort of after and a excel spreadsheet as well. Please read these in conjunction with this brief!
Updates

Dear All

I have submitted with my brief a word doc and excel spreadsheet of the two pages I want created.  However this is not the layout or design I want, I only put it together so that you will need to know what is required on each page.  Feel free to change and redesign it all.

Also the second page does not require the "process" logo or any other menu items except the first five being Home, How it works, About Us, testimonials and Contact us as per the home page.

We also are looking for something very professional and very clean.  It should be very easy to see exactly what you are looking for.

I will also extend the deadline for new designers!!  I am excited to see your talents!!

Thanks

I have increase budget and posted a note saying feel free to change all the details layout etc on my brief just include everything!!! 

Wanting a professional corporate look...

Want a professional corporate look

We have changed our minds and you we no longer require the process to be on the home page.

Thanks

Target Market(s)

Target Market

Home Inspection Companies
Pest Inspection Companies
Residential home buyers/sellers
Real Estate companies

Industry/Entity Type

It Company

Number of Pages Required

1 page

Requirements
Must have
• Colours and Styles

• The website should be mainly white as I believe it is seen as clean and simple with colour from the logos, but can be swayed if it projects the image we are after.

• It should be obvious and process orientated and I do believe symbols, pictures, etc should replace words where possible.

```html
<!DOCTYPE html>
<html lang="en">
<head>
<meta charset="utf-8">
<title>Veridian Rating – Energy Rating Job Board</title>
<link rel="stylesheet" href="https://fonts.googleapis.com/css2?family=Open+Sans:wght@400;600&family=Roboto:wght@400;500&family=Noto+Serif:ital@0;1&display=swap">
<style>
:root{
  --bg-top:#6cb838;
  --bg-mid:#2f9a45;
  --bg-bottom:#249044;
  --nav:#1f7a3f;
  --nav-dark:#17672f;
  --green-text:#4aa524;
  --teal:#2a9a55;
  --orange-a:#f2ae38;
  --orange-b:#d37a12;
  --orange-text:#d99410;
  --brand:#c05f10;
  --grey:#8a8a8a;
  --ink:#333;
  --pale:#e4f4e9;
  --row:#e6e6e6;
}
*{box-sizing:border-box;margin:0;padding:0}
html,body{width:1200px;height:2180px;overflow:hidden}
body{position:relative;background:linear-gradient(180deg,var(--bg-top) 0,var(--bg-mid) 1130px,var(--bg-top) 1168px,var(--bg-bottom) 2180px);font-family:"Roboto",Arial,sans-serif;color:var(--ink)}
.stage{position:absolute;left:0;top:0;width:1098px;height:1994px;overflow:hidden;transform:scale(1.0929);transform-origin:0 0}
.abs{position:absolute}
.panel{position:absolute;left:68px;width:965px;background:#fff;border-radius:8px;box-shadow:0 2px 6px rgba(0,0,0,.2)}
.brand-box{position:absolute;left:63px;width:332px;height:125px;background:linear-gradient(180deg,#fff,#ececec);border-radius:6px;box-shadow:0 2px 6px rgba(0,0,0,.25);display:flex;align-items:center;padding-left:24px;gap:14px}
.brand-dot{flex:none;width:58px;height:58px;border-radius:50%;background:#e8a21e}
.brand-name{font-family:"Open Sans",sans-serif;font-weight:600;font-size:30px;color:var(--brand);line-height:1;white-space:nowrap}
.nav{position:absolute;left:413px;width:600px;height:50px;background:var(--nav);border-radius:0 0 8px 8px;display:flex;align-items:center;font-family:"Open Sans",sans-serif;font-size:17px;color:#fff;white-space:nowrap}
.nav span{padding:0 11px}
.nav .current{background:var(--nav-dark);height:100%;display:flex;align-items:center;padding:0 12px;border-radius:0 0 0 8px}
.cta{position:absolute;top:95px;width:188px;height:63px;border-radius:6px;background:linear-gradient(180deg,var(--orange-a),var(--orange-b));color:#fff;font-family:"Open Sans",sans-serif;font-size:21px;text-align:center;display:flex;flex-direction:column;justify-content:center;line-height:1.1;box-shadow:0 2px 3px rgba(0,0,0,.2)}
.cta small{font-size:13px}
.process{position:absolute;left:87px;top:187px;width:924px;height:130px;background:linear-gradient(180deg,#fafafa,#ececec 50%,#fff);border-radius:8px}
.step{position:absolute;font-family:"Open Sans",sans-serif;font-size:18px;color:#444;text-align:center;line-height:19px;width:120px}
.chev{position:absolute;top:39px}
.intro{left:95px;top:337px;width:600px;font-size:17px;line-height:24px;color:var(--green-text);font-weight:500}
.lead{left:95px;top:424px;width:570px;font-size:14.5px;line-height:20px;color:#444}
.promise{position:absolute;left:64px;top:483px;width:642px;height:144px;border-radius:6px;background:linear-gradient(180deg,#fffdf8,#fde6b6);box-shadow:0 1px 4px rgba(0,0,0,.15);padding:20px 30px;color:var(--orange-text);font-size:20px;line-height:30px}
.promise p+p{font-size:24px;margin-top:16px}
.register{left:95px;top:643px;width:610px;font-size:15px;line-height:20px;color:var(--grey);font-weight:500}
.benefits{left:110px;top:716px;list-style:none;font-size:15px;line-height:20px;color:#444}
.benefits li{padding-left:21px;position:relative}
.benefits li::before{content:"";position:absolute;left:2px;top:6px;border-left:6px solid #8bbd3a;border-top:4px solid transparent;border-bottom:4px solid transparent}
.free{left:95px;top:873px;width:580px;font-size:15px;line-height:20px;font-weight:500;color:#222}
.login{position:absolute;left:724px;top:337px;width:312px;height:185px;background:linear-gradient(180deg,#5da52c,#a9c73a);border-radius:6px;box-shadow:0 2px 5px rgba(0,0,0,.2);color:#fff}
.login label{position:absolute;font-family:"Open Sans",sans-serif;font-size:19px;padding-left:20px}
.login label::before,.bullet::before{content:"";position:absolute;left:2px;top:8px;width:8px;height:8px;border-radius:50%;background:#c8e36a;border:2px solid #2c6d1f}
.field{position:absolute;width:267px;height:31px;background:#fff;border-radius:5px;box-shadow:inset 0 1px 3px rgba(0,0,0,.3);font-size:15px;color:#888;padding:6px 9px}
.forgot{position:absolute;left:22px;top:158px;font-size:12px}
.testi{position:absolute;left:724px;top:555px;width:289px;height:392px;background:linear-gradient(180deg,#f1f1f1,#fff 20%,#fff 85%,#f1f1f1);border-radius:8px}
.testi h2{position:absolute;left:12px;top:10px;font-family:"Open Sans",sans-serif;font-weight:400;font-size:26px;color:var(--teal)}
.quote{position:absolute;font-family:"Noto Serif",serif;font-size:12.5px;line-height:18px;color:#888;text-align:right;width:140px}
.mark{position:absolute;font-family:"Noto Serif",serif;font-size:42px;color:#7fb52e;line-height:1}
.who{position:absolute;font-family:"Noto Serif",serif;font-style:italic;font-size:11px;color:#333}
.who b{font-size:13px;display:block;font-weight:400}
.portrait{position:absolute;width:80px;height:80px;border:2px solid #f0a020;background:linear-gradient(160deg,#a57b55,#4a3b30)}
.foot{position:absolute;left:68px;font-size:11.5px;color:#a9e08a}
.welcome{position:absolute;left:425px;top:1178px;color:#c8650f;font-size:30px;padding-left:24px;font-weight:500;white-space:nowrap}
.welcome span{font-size:24px;font-weight:400}
.bullet{position:relative}
.welcome.bullet::before{top:14px;left:0}
.btn{position:absolute;height:28px;border-radius:5px;background:linear-gradient(180deg,#fafafa,#d9d9d9);border:1px solid #ccc;font-size:12.5px;color:#555;display:flex;align-items:center;gap:6px;padding:0 8px}
.details{position:absolute;left:87px;top:1253px;width:920px;height:173px;background:linear-gradient(180deg,#f3f3f3,#fff 40%,#fff 80%,#f3f3f3);border-radius:8px}
.details h2{position:absolute;left:22px;top:16px;font-family:"Noto Serif",serif;font-weight:400;font-size:25px;color:var(--teal)}
.dl{position:absolute;font-size:14px;color:#8ab72e;padding-left:15px}
.dl::before{content:"";position:absolute;left:0;top:7px;width:5px;height:5px;border-radius:50%;background:#6aa32a}
.dv{position:absolute;font-family:"Noto Serif",serif;font-size:17px;color:#444}
.tab{position:absolute;top:1468px;height:38px;border-radius:6px 6px 0 0;color:#fff;font-family:"Open Sans",sans-serif;font-size:18px;display:flex;align-items:center;justify-content:center;white-space:nowrap}
.board{position:absolute;left:98px;top:1505px;width:903px;height:411px;background:linear-gradient(180deg,#78a62e,#a9c83a);border-radius:4px}
.jobs{position:absolute;left:112px;width:873px;background:#fff;border-radius:5px;overflow:hidden;font-size:11px;color:#333}
.jobs .head{position:relative;height:54px;background:var(--pale);font-size:12px;font-weight:500;color:#4aa524;line-height:19px}
.jobs .head span,.jobs .r span{position:absolute;white-space:nowrap}
.jobs .head span{top:9px}
.r{position:absolute;left:110px;width:763px;height:36px}
.r span{top:11px}
.job-name{position:absolute;left:8px;font-size:11px;font-weight:500;color:#3a9a3a;padding-left:15px}
.job-name::before{content:"+";position:absolute;left:0;top:-6px;font-size:19px;font-weight:700;color:#5aa52a}
.ic{position:absolute;top:9px}
</style>
</head>
<body>
<div class="stage">

  <!-- Home page -->
  <section class="panel" style="top:30px;height:978px"></section>
  <div class="brand-box" style="top:37px"><span class="brand-dot"></span><span class="brand-name">Veridian Rating</span></div>
  <nav class="nav" style="top:28px"><span class="current">HOME</span><span>HOW IT WORKS?</span><span>ABOUT US</span><span>TESTIMONIALS</span><span>CONTACT US</span></nav>
  <a class="cta" style="left:420px">GET A QUOTE</a>
  <a class="cta" style="left:619px">ENERGY RATERS<small>Add your business</small></a>
  <a class="cta" style="left:818px">ACTIVE<br>JOB BOARD</a>

  <div class="process">
    <div class="step" style="left:19px;top:56px">Post a job</div>
    <svg class="chev" style="left:165px" width="36" height="52" viewBox="0 0 36 52"><path d="M4 2 L30 26 L4 50 L4 38 L18 26 L4 14Z" fill="#2f9a45"/></svg>
    <div class="step" style="left:210px;top:35px">Get as many quotes as you like</div>
    <svg class="chev" style="left:350px" width="36" height="52" viewBox="0 0 36 52"><path d="M4 2 L30 26 L4 50 L4 38 L18 26 L4 14Z" fill="#2f9a45"/></svg>
    <div class="step" style="left:398px;top:34px">Select energy quote that suits</div>
    <svg class="chev" style="left:537px" width="36" height="52" viewBox="0 0 36 52"><path d="M4 2 L30 26 L4 50 L4 38 L18 26 L4 14Z" fill="#2f9a45"/></svg>
    <div class="step" style="left:586px;top:43px">Approve payment</div>
    <svg class="chev" style="left:723px" width="36" height="52" viewBox="0 0 36 52"><path d="M4 2 L30 26 L4 50 L4 38 L18 26 L4 14Z" fill="#2f9a45"/></svg>
    <div class="step" style="left:761px;top:46px">Receive Rating</div>
  </div>

  <p class="abs intro">We provide you with solutions to your energy rating needs!&nbsp; Get up to 10 competitive quotes for your energy ratings from our database of professional accredited energy raters in all states and territories!</p>
  <p class="abs lead">Veridian Rating is Australia's leading professional energy rating consultancy firm specializing in large scaled residential and commercial energy rating logistics.</p>
  <div class="promise"><p>It's Free, Fast and Easy to use and you get the best price and turnaround time that suits you!!</p><p>Its a one stop shop for your energy rating needs!!</p></div>
  <p class="abs register">Register with us, upload your job and specifications, and sit back and watch as energy raters provide quotes for your work!</p>
  <ul class="abs benefits">
    <li>Get up to 10 best priced quotes for your energy ratings</li>
    <li>You save time</li>
    <li>Be able to specify your desired turnaround times</li>
    <li>You can upload a job for quoting anytime and anywhere</li>
    <li>Choose a deadline for energy raters to supply quotes</li>
    <li>Be able to track your numerous jobs in one place</li>
  </ul>
  <p class="abs free">Its totally free to be registered with us and there is no obligations or hidden catches!</p>

  <form class="login">
    <label style="left:20px;top:11px">User</label>
    <div class="field" style="left:20px;top:39px">cweston</div>
    <label style="left:21px;top:86px">Password</label>
    <div class="field" style="left:22px;top:114px;color:#333;letter-spacing:1px">●●●●●●●●●●</div>
    <span class="forgot">Did you forget your password</span>
  </form>

  <aside class="testi">
    <h2>TESTIMONIALS</h2>
    <span class="mark" style="left:8px;top:50px">“</span>
    <p class="quote" style="left:40px;top:51px">Lorem ipsum dolor sit amet, consectetur adipiscing elit. Phasellus arcu magna, condimentum id consequat quis,</p>
    <div class="portrait" role="img" aria-label="Portrait of customer Helen Marsh" style="left:191px;top:54px"></div>
    <p class="who" style="left:16px;top:172px"><b>Helen Marsh</b>Port Elmer, Westland</p>
    <span class="mark" style="left:246px;top:180px">”</span>
    <span class="mark" style="left:8px;top:235px">“</span>
    <p class="quote" style="left:40px;top:236px">Lorem ipsum dolor sit amet, consectetur adipiscing elit. Phasellus arcu</p>
    <div class="portrait" role="img" aria-label="Portrait of customer Tom Reilly" style="left:191px;top:239px;background:linear-gradient(160deg,#cfcfcf,#3a3a3a)"></div>
    <p class="who" style="left:17px;top:337px"><b>Tom Reilly</b>Ridgeway, Northland</p>
    <span class="mark" style="left:246px;top:345px">”</span>
  </aside>

  <p class="foot" style="top:1019px">Copyright 2010 - Veridian Rating - All rights reserved</p>

  <!-- Client job board -->
  <section class="panel" style="top:1098px;height:859px"></section>
  <div class="brand-box" style="top:1106px"><span class="brand-dot"></span><span class="brand-name">Veridian Rating</span></div>
  <nav class="nav" style="top:1097px"><span class="current">HOME</span><span>HOW IT WORKS?</span><span>ABOUT US</span><span>TESTIMONIALS</span><span>CONTACT US</span></nav>

  <h1 class="welcome bullet">Welcome, <span>Clara Weston</span></h1>
  <a class="btn" style="left:836px;top:1189px;width:94px"><svg width="22" height="16" viewBox="0 0 22 16"><path d="M1 8 L9 1 V5 H21 V11 H9 V15Z" fill="#c8201c"/></svg>Logout</a>
  <a class="btn" style="left:943px;top:1189px;width:68px"><svg width="14" height="18" viewBox="0 0 14 18"><text x="1" y="16" font-size="18" font-weight="700" fill="#1c5fb0" font-family="Arial,sans-serif">?</text></svg>Help</a>

  <div class="details">
    <h2>Personal details</h2>
    <a class="btn" style="left:802px;top:12px;width:106px"><svg width="18" height="18" viewBox="0 0 18 18"><path d="M3 15 L4 11 L13 2 L16 5 L7 14Z" fill="#f0a020"/><path d="M2 17 H16" stroke="#c8201c" stroke-width="1.5"/></svg>Edit profile</a>
    <span class="dl" style="left:43px;top:70px">Company</span><span class="dv" style="left:181px;top:64px">Veridian Rating</span>
    <span class="dl" style="left:43px;top:100px">Contact Name</span><span class="dv" style="left:181px;top:96px">Sam Porter</span>
    <span class="dl" style="left:43px;top:130px">E-mail address</span><span class="dv" style="left:181px;top:131px;font-family:Roboto,sans-serif;font-size:10px;color:#2a9a55">sporter@veridian-rating.example</span>
    <span class="dl" style="left:469px;top:70px">Address</span>
    <span class="dv" style="left:579px;top:64px;line-height:30px">14 Harbour Lane<br>LINDALE VIC 3999</span>
  </div>

  <a class="tab" style="left:104px;width:146px;background:linear-gradient(180deg,#e9a33a,#c8700f);color:#fde6b8">QUOTING JOBS</a>
  <a class="tab" style="left:259px;width:129px;background:var(--nav)">ACTIVE JOBS</a>
  <a class="tab" style="left:396px;width:167px;background:var(--nav)">COMPLEATE JOBS</a>
  <a class="tab" style="left:799px;width:186px;background:linear-gradient(180deg,#6d9a2c,#5a8a22);gap:10px"><svg width="16" height="16" viewBox="0 0 16 16"><path d="M6 1H10V6H15V10H10V15H6V10H1V6H6Z" fill="#c5e07a"/></svg>ADD A NEW JOB</a>

  <div class="board"></div>

  <div class="jobs" style="top:1522px;height:162px">
    <div class="head"><span style="left:51px">JOB</span><span style="left:123px">QUOTE NUMBER</span><span style="left:245px">PRICE</span><span style="left:306px">TOTAL PRICE</span><span style="left:410px;text-align:center">TURNAROUND<br>TIME</span><span style="left:517px">REWORK PRICE</span><span style="left:636px">ENERGY RATERS<br>ACCREDITATION</span></div>
    <span class="job-name" style="top:98px">Elm Court</span>
    <div class="r" style="top:54px;background:var(--row)"><span style="left:13px">111111</span><span style="left:130px">$155,00</span><span style="left:196px">$180,65</span><span style="left:301px">1-5 days</span><span style="left:410px">$120,00</span><span style="left:527px">VIC</span>
      <svg class="ic" style="left:643px" width="16" height="16" viewBox="0 0 16 16"><path d="M2 9 L6 13 L14 3" stroke="#5aa52a" stroke-width="3" fill="none"/></svg>
      <svg class="ic" style="left:681px" width="16" height="16" viewBox="0 0 16 16"><path d="M3 3 L13 13 M13 3 L3 13" stroke="#c8201c" stroke-width="3.5"/></svg>
      <svg class="ic" style="left:719px" width="24" height="16" viewBox="0 0 24 16"><rect x="1" y="1" width="22" height="14" fill="#fafafa" stroke="#bbb"/><path d="M1 1 L12 9 L23 1" stroke="#bbb" fill="none"/></svg></div>
    <div class="r" style="top:90px;background:#fff"><span style="left:13px">111156</span><span style="left:130px">$250,00</span><span style="left:196px">$265,00</span><span style="left:301px">5-10 days</span><span style="left:410px">$150,00</span><span style="left:527px">QLD</span>
      <svg class="ic" style="left:643px" width="16" height="16" viewBox="0 0 16 16"><path d="M2 9 L6 13 L14 3" stroke="#5aa52a" stroke-width="3" fill="none"/></svg>
      <svg class="ic" style="left:681px" width="16" height="16" viewBox="0 0 16 16"><path d="M3 3 L13 13 M13 3 L3 13" stroke="#c8201c" stroke-width="3.5"/></svg>
      <svg class="ic" style="left:719px" width="24" height="16" viewBox="0 0 24 16"><rect x="1" y="1" width="22" height="14" fill="#fafafa" stroke="#bbb"/><path d="M1 1 L12 9 L23 1" stroke="#bbb" fill="none"/></svg></div>
    <div class="r" style="top:126px;background:var(--row)"><span style="left:13px">111186</span><span style="left:130px">$125,00</span><span style="left:196px">$129,65</span><span style="left:301px">2 weeks</span><span style="left:410px">$100,00</span><span style="left:527px">SA</span>
      <svg class="ic" style="left:643px" width="16" height="16" viewBox="0 0 16 16"><path d="M2 9 L6 13 L14 3" stroke="#5aa52a" stroke-width="3" fill="none"/></svg>
      <svg class="ic" style="left:681px" width="16" height="16" viewBox="0 0 16 16"><path d="M3 3 L13 13 M13 3 L3 13" stroke="#c8201c" stroke-width="3.5"/></svg>
      <svg class="ic" style="left:719px" width="24" height="16" viewBox="0 0 24 16"><rect x="1" y="1" width="22" height="14" fill="#fafafa" stroke="#bbb"/><path d="M1 1 L12 9 L23 1" stroke="#bbb" fill="none"/></svg></div>
  </div>

  <div class="jobs" style="top:1700px;height:197px">
    <div class="head"><span style="left:51px">JOB</span><span style="left:123px">QUOTE NUMBER</span><span style="left:245px">PRICE</span><span style="left:306px">TOTAL PRICE</span><span style="left:410px;text-align:center">TURNAROUND<br>TIME</span><span style="left:517px">REWORK PRICE</span><span style="left:636px">ENERGY RATERS<br>ACCREDITATION</span></div>
    <span class="job-name" style="top:98px">Elm Court</span>
    <div class="r" style="top:54px;background:var(--row)"><span style="left:13px">111111</span><span style="left:130px">$155,00</span><span style="left:196px">$180,65</span><span style="left:301px">1-5 days</span><span style="left:410px">$120,00</span><span style="left:527px">VIC</span>
      <svg class="ic" style="left:643px" width="16" height="16" viewBox="0 0 16 16"><path d="M2 9 L6 13 L14 3" stroke="#5aa52a" stroke-width="3" fill="none"/></svg>
      <svg class="ic" style="left:681px" width="16" height="16" viewBox="0 0 16 16"><path d="M3 3 L13 13 M13 3 L3 13" stroke="#c8201c" stroke-width="3.5"/></svg>
      <svg class="ic" style="left:719px" width="24" height="16" viewBox="0 0 24 16"><rect x="1" y="1" width="22" height="14" fill="#fafafa" stroke="#bbb"/><path d="M1 1 L12 9 L23 1" stroke="#bbb" fill="none"/></svg></div>
    <div class="r" style="top:90px;background:#fff"><span style="left:13px">111156</span><span style="left:130px">$250,00</span><span style="left:196px">$265,00</span><span style="left:301px">5-10 days</span><span style="left:410px">$150,00</span><span style="left:527px">QLD</span>
      <svg class="ic" style="left:643px" width="16" height="16" viewBox="0 0 16 16"><path d="M2 9 L6 13 L14 3" stroke="#5aa52a" stroke-width="3" fill="none"/></svg>
      <svg class="ic" style="left:681px" width="16" height="16" viewBox="0 0 16 16"><path d="M3 3 L13 13 M13 3 L3 13" stroke="#c8201c" stroke-width="3.5"/></svg>
      <svg class="ic" style="left:719px" width="24" height="16" viewBox="0 0 24 16"><rect x="1" y="1" width="22" height="14" fill="#fafafa" stroke="#bbb"/><path d="M1 1 L12 9 L23 1" stroke="#bbb" fill="none"/></svg></div>
    <div class="r" style="top:126px;background:var(--row)"><span style="left:13px">111186</span><span style="left:130px">$125,00</span><span style="left:196px">$129,65</span><span style="left:301px">2 weeks</span><span style="left:410px">$100,00</span><span style="left:527px">SA</span>
      <svg class="ic" style="left:643px" width="16" height="16" viewBox="0 0 16 16"><path d="M2 9 L6 13 L14 3" stroke="#5aa52a" stroke-width="3" fill="none"/></svg>
      <svg class="ic" style="left:681px" width="16" height="16" viewBox="0 0 16 16"><path d="M3 3 L13 13 M13 3 L3 13" stroke="#c8201c" stroke-width="3.5"/></svg>
      <svg class="ic" style="left:719px" width="24" height="16" viewBox="0 0 24 16"><rect x="1" y="1" width="22" height="14" fill="#fafafa" stroke="#bbb"/><path d="M1 1 L12 9 L23 1" stroke="#bbb" fill="none"/></svg></div>
    <div class="r" style="top:162px;background:#fff"><span style="left:13px">111313</span><span style="left:130px">$350,00</span><span style="left:196px">$354,65</span><span style="left:301px">Aluminum</span><span style="left:410px">Doors</span><span style="left:527px">Standard</span></div>
  </div>

  <p class="foot" style="top:1970px">Copyright 2010 - Veridian Rating - All rights reserved</p>
</div>
</body>
</html>
```